Health Spectrum and Energy Slides

Create beautiful and facinating PowerPoint slides that inspire and motivate

Target Market(s)

Clients looking for strategic breakthroughs and transformation

Industry/Entity Type

Health

Requirements
Must have
• Beautiful, heartfelt and fascinating graphics.
Nice to have
• Award winning designs.

```html
<!DOCTYPE html>
<html lang="en">
<head>
<meta charset="utf-8">
<title>Health Spectrum</title>
<link href="https://fonts.googleapis.com/css2?family=Open+Sans:wght@400&display=swap" rel="stylesheet">
<style>
  :root {
    --bg: #c9cacc;
    --ink: #1b1b1b;
    --frame: #000000;
    --circle: #5b9bd5;
    --circle-edge: #4a86bf;
    --circle-ink: #15212e;
    --glow: #ffffff;
  }
  html, body {
    margin: 0;
    padding: 0;
    overflow: hidden;
    background: var(--bg);
  }
  .slide {
    position: relative;
    width: 1200px;
    height: 675px;
    overflow: hidden;
    background: var(--bg);
    font-family: "Open Sans", sans-serif;
    color: var(--ink);
  }
  .centre-art {
    position: absolute;
    left: 445px;
    top: 20px;
    width: 350px;
    height: 320px;
    border-radius: 50%;
    background: radial-gradient(ellipse at 50% 55%, var(--glow) 0%, rgba(255,255,255,0.85) 35%, rgba(255,255,255,0) 70%);
  }
  .spectrum-frame {
    position: absolute;
    left: 0;
    top: 0;
    width: 1200px;
    height: 675px;
  }
  .stage-label {
    position: absolute;
    font-size: 12.7px;
    line-height: 18px;
    margin: 0;
  }
  .stage-label--decline {
    right: 849px;
    text-align: right;
  }
  .stage-label--rise {
    text-align: left;
  }
  .spectrum-badge {
    position: absolute;
    top: 255px;
    width: 218px;
    height: 218px;
    border-radius: 50%;
    background: var(--circle);
    border: 1px solid var(--circle-edge);
    display: flex;
    align-items: center;
    justify-content: center;
    text-align: center;
    color: var(--circle-ink);
    font-size: 18.5px;
    line-height: 27px;
    margin: 0;
  }
  .spectrum-badge--decline { left: 10px; }
  .spectrum-badge--rise { left: 972px; }
</style>
</head>
<body>
<main class="slide">
  <div class="centre-art" role="img" aria-label="Glowing illustration of a head in profile with a colourful wheel and circular arrow pointing down"></div>

  <svg class="spectrum-frame" viewBox="0 0 1366 768" preserveAspectRatio="none" aria-hidden="true">
    <path d="M424,127 V686 H966 V123" fill="none" stroke="var(--frame)" stroke-width="10"/>
    <path d="M465,127 C510,138 512,240 545,265 C580,292 618,330 640,380 C662,422 705,440 780,446 C838,451 850,515 865,572 C881,632 915,658 952,672"
          fill="none" stroke="var(--frame)" stroke-width="5" stroke-linecap="round"/>
  </svg>

  <p class="stage-label stage-label--decline" style="top:120px">Optimal Health<br>Emotional, Biological,<br>Structural &amp; Spiritual</p>
  <p class="stage-label stage-label--decline" style="top:202px">Subconscious<br>Stress</p>
  <p class="stage-label stage-label--decline" style="top:261px">Subtle Dis-Stress &amp;<br>Dis-Ease<br>Ache</p>
  <p class="stage-label stage-label--decline" style="top:354px">Acute Dis-Stress &amp;<br>Dis-Ease Pain</p>
  <p class="stage-label stage-label--decline" style="top:441px;right:842px">Chronic Dis-Stress &amp;<br>Dis-Ease<br>Severe Pain</p>
  <p class="stage-label stage-label--decline" style="top:548px">Death Physical<br>Emotional,<br>Biological, Structural</p>

  <p class="stage-label stage-label--rise" style="left:863px;top:116px">Transformation: Conscious<br>Heartful Intentional<br>Choice &amp; Action</p>
  <p class="stage-label stage-label--rise" style="left:863px;top:215px">Change:<br>Conscious Choice &amp; Action</p>
  <p class="stage-label stage-label--rise" style="left:863px;top:264px">Conscious Awareness</p>
  <p class="stage-label stage-label--rise" style="left:863px;top:348px">Therapy</p>
  <p class="stage-label stage-label--rise" style="left:872px;top:430px">Trauma:<br>Subconscious<br>Automatic Reaction</p>
  <p class="stage-label stage-label--rise" style="left:872px;top:536px">Death Physical<br>Emotional, Biological,<br>Structural</p>

  <h2 class="spectrum-badge spectrum-badge--decline">Optimal Health to<br>Death Maladaptive<br>Dis-Stress<br>Reaction Spectrum</h2>
  <h2 class="spectrum-badge spectrum-badge--rise">Transformation to<br>Death Adaptive<br>Response Spectrum</h2>
</main>
</body>
</html>
```